Web Page Design for a Website that Provides Tutoring

I am looking to create an online tutoring website. The website will allow parents or students to contact tutors with a view to instructing them to tutor themselves or their children.

The name of the website is LendYourLessons.

This brief is to create the design for one of the web pages for this web site. I am hoping the same designer will be available to design other pages.

The page I want designed is one of the more complex and I have attached the design as an excel spreadsheet. The web page needs to include all the items on this page but if you want to change the positioning of the items then Im fine with that.

I recently had two logos created for this website. My favourite is the one with a mortar board but im not sure I like the colours. I have attached both of these logos and you can use either of them, change the colours or create something different. I just want a design pleasing to the eye. If the logo is changed I would like that in a seperate file.

So can you please submit designs for this page. I have attached the two logos which you can use, change or if you feel you have a better idea then you can use that.

On the spreadsheet the Send Message, Favourite etc are buttons.

Target Market(s)

People who want to better themselves.
Possible middle class to upper class.

Industry/Entity Type

Tutoring

Number of Pages Required

1 page

Requirements
Must have
• The designs must have alot of the information attached in the spreadsheet.

```html
<!DOCTYPE html>
<html lang="en">
<head>
<meta charset="utf-8">
<title>LendYourLessons – Tutor Profile</title>
<link href="https://fonts.googleapis.com/css2?family=Roboto:wght@300;400;500;700&family=Raleway:wght@400;500&display=swap" rel="stylesheet">
<style>
:root{
  --orange:#f7941d;
  --coral:#ff6a45;
  --navy:#2f5496;
  --footer:#3e6cb3;
  --dark:#2b2f36;
  --text:#333;
  --muted:#666;
  --line:#d6d6d6;
  --panel:#eef1fb;
  --avail:#d7fbd0;
  --star:#ff6a45;
  --star-off:#b5b5b5;
}
*{box-sizing:border-box;margin:0;padding:0}
html,body{width:898px;height:1200px;overflow:hidden}
body{position:relative;background:#fff;font-family:Roboto,Arial,sans-serif;color:var(--text);font-size:10px}
.abs{position:absolute}
/* header */
.site-header{position:absolute;left:0;top:0;width:898px;height:70px;background:#fff}
.brand{left:60px;top:22px;font-size:22px;font-weight:700;color:var(--orange);letter-spacing:-.3px}
.brand .dot{display:inline-block;width:10px;height:10px;background:var(--navy);margin-right:5px;vertical-align:middle}
.nav a{position:absolute;top:30px;font-size:11.5px;color:#222;text-decoration:none}
.nav a.active{color:var(--navy);border-bottom:1px solid var(--navy);padding-bottom:2px}
.btn{position:absolute;display:flex;align-items:center;justify-content:center;color:#fff;font-size:10.5px;font-weight:500;border-radius:2px;box-shadow:1px 2px 0 rgba(0,0,0,.2)}
.btn-login{left:691px;top:22px;width:69px;height:27px;background:var(--orange)}
.btn-register{left:768px;top:22px;width:69px;height:27px;background:var(--coral)}
.breadcrumb{position:absolute;left:0;top:70px;width:898px;height:41px;background:var(--dark);color:#cfd3da;font-size:13px;font-weight:300;padding:11px 0 0 59px}
/* cards */
.card{position:absolute;border:1px solid var(--line);background:#fff}
.card-head{height:26px;background:var(--orange);color:#fff;font-size:12px;font-weight:500;padding:6px 8px}
.card-head.coral{background:var(--coral);padding-left:12px}
.stars{display:flex;gap:2px}
.stars svg{width:13px;height:13px}
.on{fill:var(--star)}.off{fill:var(--star-off)}
/* profile */
.profile{left:59px;top:136px;width:513px;height:162px}
.profile .photo{left:11px;top:11px;width:128px;height:136px;background:linear-gradient(160deg,#6d7380,#3b3f48 60%,#9fb3cc)}
.profile .name{left:158px;top:11px;font-size:16px;color:#222}
.profile .degree{left:158px;top:33px;width:150px;font-size:9px;color:var(--muted);line-height:12px}
.facts{position:absolute;font-size:9px;line-height:18.5px;color:var(--muted)}
.facts b{color:#222;font-weight:500}
.profile .side{left:318px;top:0;width:194px;height:160px;background:var(--panel)}
/* tutor info */
.info{left:59px;top:318px;width:513px;height:161px}
.info .letter{left:19px;top:40px;width:282px;font-size:9px;line-height:12px;color:#444}
.info .divider{left:320px;top:40px;width:1px;height:100px;background:var(--line)}
.info .qual{left:335px;top:40px;width:160px;font-size:9px;line-height:12px;color:#444}
.info .scroll{left:507px;top:34px;width:2px;height:108px;background:#ddd}
.info .scroll i{display:block;height:16px;background:var(--coral)}
/* tables */
.subjects{left:59px;top:500px;width:513px;height:115px}
.subjects table{border-collapse:collapse;width:503px;margin-left:0}
.subjects th{background:#d9d9d9;font-weight:400;font-size:9px;color:#444;height:26px;text-align:left}
.subjects td{font-size:10px;height:22px;border-bottom:1px solid #e3e3e3;text-align:left}
.subjects td:first-child{padding-left:11px;color:#222}
.subjects tr:last-child td{border:none}
.avail{left:59px;top:636px;width:513px;height:175px}
.avail .days{left:0;top:28px;width:511px;height:22px;background:#d9d9d9}
.avail .days span{position:absolute;top:5px;font-size:9px;color:#444;transform:translateX(-50%)}
.avail .grid{left:75px;top:61px;width:425px;height:68px;background:var(--avail)}
.avail .time{left:11px;font-size:9px;color:#222}
.bar{position:absolute;width:40px;height:8px}
.legend{left:75px;top:147px;font-size:9px;color:var(--muted);display:flex;gap:12px;align-items:center}
.legend b{font-weight:500;color:#222}
.legend i{display:inline-block;width:7px;height:7px;margin-right:4px}
/* contact */
.contact{left:591px;top:136px;width:247px;height:314px;background:var(--panel)}
.field-label{left:13px;font-size:10px;color:#777}
.input{position:absolute;left:80px;width:153px;height:23px;background:#fff;border:1px solid #c9c9c9;border-radius:2px}
.textarea{left:14px;top:178px;width:219px;height:76px}
.btn-submit{left:165px;top:269px;width:68px;height:24px;background:var(--navy);box-shadow:none;font-weight:700}
/* reviews */
.reviews{left:591px;top:471px;width:247px;height:342px;background:var(--panel)}
.review{position:absolute;left:14px;width:219px;height:135px;background:#fff;border:1px solid var(--line);background:var(--panel)}
.review .avatar{position:absolute;left:13px;top:11px;width:43px;height:43px;border:1px solid #ccc}
.review .stars{position:absolute;left:66px;top:36px}
.review blockquote{position:absolute;left:12px;top:62px;width:195px;font-size:9px;line-height:12px;color:#333;padding-left:8px}
.review cite{position:absolute;left:20px;top:115px;font-style:normal;font-size:9px;color:#222}
/* footer */
.site-footer{position:absolute;left:0;top:875px;width:898px;height:285px;background:linear-gradient(100deg,#3c68ad,#4a77bd 45%,#3b67ab)}
.site-footer h3{position:absolute;top:33px;font-family:Raleway,sans-serif;font-weight:400;font-size:16px;color:var(--orange);padding-bottom:6px;border-bottom:1px solid rgba(255,255,255,.35)}
.qlinks{left:62px;top:90px;list-style:none;font-size:10.5px;color:#fff;line-height:20px}
.qlinks li::before{content:"›";margin-right:5px;font-size:9px}
.cinfo{left:226px;top:86px;width:215px;font-size:9.5px;color:#fff;line-height:12px}
.cinfo .row{position:relative;padding-left:15px;margin-bottom:10px}
.cinfo svg{position:absolute;left:0;top:1px;width:9px;height:10px;fill:#fff}
.cinfo .call{color:var(--orange);font-size:12px}
.nl-text{left:479px;top:86px;width:170px;font-size:8px;color:#fff;line-height:12px}
.nl-input{left:479px;top:118px;width:151px;height:18px;background:#fff;font-size:8px;color:#888;padding:5px 7px}
.btn-sub{left:479px;top:147px;width:55px;height:16px;background:var(--orange);font-size:9px;box-shadow:none;border-radius:0}
.follow{left:699px;top:90px;font-size:10px;color:#fff}
.follow div{display:flex;align-items:center;height:25px}
.follow i{display:inline-block;width:18px;height:18px;border-radius:2px;margin-right:9px;background:rgba(255,255,255,.25)}
.bottom-bar{position:absolute;left:0;top:1160px;width:898px;height:40px;background:var(--orange);color:#fff;font-size:8.5px;padding:15px 56px;display:flex;justify-content:space-between}
</style>
</head>
<body>
<svg width="0" height="0" style="position:absolute"><defs><symbol id="star" viewBox="0 0 24 24"><path d="M12 1.5l3.1 7 7.4.6-5.6 4.9 1.7 7.3L12 17.4l-6.6 3.9 1.7-7.3-5.6-4.9 7.4-.6z"/></symbol></defs></svg>

<header class="site-header">
  <div class="abs brand"><span class="dot"></span>LendYourLessons</div>
  <nav class="nav">
    <a style="left:358px">Home</a><a class="active" style="left:411px">Search</a><a style="left:468px">Student</a><a style="left:531px">Tutor</a><a style="left:585px">About</a><a style="left:639px">Contact</a>
  </nav>
  <div class="btn btn-login">Login</div>
  <div class="btn btn-register">Register</div>
</header>
<div class="breadcrumb">Home &gt; Search &gt; Teacher Name</div>

<section class="card profile">
  <div class="abs photo" role="img" aria-label="Portrait photo of the tutor"></div>
  <div class="abs name">Daniel Hart</div>
  <div class="abs degree">Bachelor Degree in History from the University of Northfield</div>
  <div class="facts" style="left:158px;top:63px"><b>Subject:</b> Biology<br><b>Age:</b> 24<br><b>Tutoring Type :</b> Lorem Ipsum<br><b>Willing To Travel:</b> Lorem Ipsum</div>
  <div class="abs side">
    <div class="abs" style="left:15px;top:7px;font-size:9px;font-weight:500;color:#222">Feedback Score:</div>
    <div class="abs stars" style="left:15px;top:21px"><svg class="on"><use href="#star"/></svg><svg class="on"><use href="#star"/></svg><svg class="on"><use href="#star"/></svg><svg class="on"><use href="#star"/></svg><svg class="off"><use href="#star"/></svg></div>
    <div class="facts" style="left:15px;top:52px"><b>Education:</b> Lorem Ipsum<br><b>Age:</b> 21<br><b>Response Rate:</b> 75%<br><b>Expected Response:</b> &lt; 20 hours</div>
  </div>
</section>

<section class="card info">
  <div class="card-head">Tutor Informtion</div>
  <div class="abs letter">Hello,<br><br>My name is Daniel Hart, and I am a Historian specialized in languages and Ancient History. I am from Barcelona but I studied in different places of Spain. I have a Bachelor Degree in History from the University of Northfield. This degree is structured in a significant freedom of subjects choice (three years studying universal, general and heoretical History and two years studying Ancient History, Art, Languages and Beliefs). Besides, I started an Undergraduate</div>
  <div class="abs divider"></div>
  <div class="abs qual"><b style="font-weight:500;color:#222">Qualification</b><br><br>Bachelor Degree in History from the University of Northfield Undergraduate Degree in Classical Studies from Eastbridge University</div>
  <div class="abs scroll"><i></i></div>
</section>

<section class="card subjects">
  <div class="card-head">Subjects Taught</div>
  <table>
    <colgroup><col style="width:93px"><col style="width:55px"><col style="width:64px"><col style="width:58px"><col style="width:58px"><col style="width:75px"><col></colgroup>
    <tr><th></th><th>Primary</th><th>Secondary</th><th>GCSE</th><th>A-LEVEL</th><th>University</th><th>Adult Learner</th></tr>
    <tr><td>Biology</td><td>£20</td><td>£20</td><td>£50</td><td></td><td>£20</td><td>£20</td></tr>
    <tr><td>Chemistry</td><td>£20</td><td>£30</td><td>£20</td><td></td><td>£20</td><td>£20</td></tr>
  </table>
</section>

<section class="card avail">
  <div class="card-head">Availability</div>
  <div class="abs days"><span style="left:95px">Mon Day</span><span style="left:159px">Tues Day</span><span style="left:229px">Wednes Day</span><span style="left:301px">Thurs Day</span><span style="left:366px">Fri Day</span><span style="left:425px">Satur Day</span><span style="left:482px">Sun Day</span></div>
  <div class="abs grid"></div>
  <div class="abs time" style="top:65px">7-8PM</div>
  <div class="abs time" style="top:90px">8-9PM</div>
  <div class="abs time" style="top:116px">4-5PM</div>
  <div class="bar" style="left:207px;top:74px;background:var(--coral)"></div>
  <div class="bar" style="left:207px;top:91px;background:var(--orange)"></div>
  <div class="bar" style="left:207px;top:112px;background:var(--navy)"></div>
  <div class="bar" style="left:461px;top:86px;background:var(--navy)"></div>
  <div class="bar" style="left:345px;top:112px;background:var(--orange)"></div>
  <div class="abs legend"><b>Legend:</b><span><i style="background:var(--avail)"></i>Available</span><span><i style="background:var(--coral)"></i>Taken</span><span><i style="background:var(--orange)"></i>Reserved</span><span><i style="background:var(--navy)"></i>No</span></div>
</section>

<aside class="card contact">
  <div class="card-head coral">Contact Daniel Hart</div>
  <div class="abs field-label" style="top:46px">Email</div><div class="input" style="top:41px"></div>
  <div class="abs field-label" style="top:80px">Name</div><div class="input" style="top:75px"></div>
  <div class="abs field-label" style="top:114px">Postcode</div><div class="input" style="top:109px"></div>
  <div class="abs field-label" style="top:148px">Phone</div><div class="input" style="top:143px"></div>
  <div class="input textarea"></div>
  <div class="btn btn-submit">SUBMIT</div>
</aside>

<aside class="card reviews">
  <div class="card-head coral">Tutors Review</div>
  <article class="review" style="top:42px">
    <div class="avatar" role="img" aria-label="Student profile photo" style="background:linear-gradient(160deg,#c9b9a6,#7a5a44)"></div>
    <div class="stars"><svg class="on"><use href="#star"/></svg><svg class="on"><use href="#star"/></svg><svg class="on"><use href="#star"/></svg><svg class="on"><use href="#star"/></svg><svg class="off"><use href="#star"/></svg></div>
    <blockquote>“Lorem ipsum dolor sit amet, consectetur adipiscing elit. Donec et quam nunc. Nam tortor sapien, volutpat consectetur lacus ut, accumsan viverra urna. ”</blockquote>
    <cite>- Student Name</cite>
  </article>
  <article class="review" style="top:189px">
    <div class="avatar" role="img" aria-label="Student profile photo" style="background:linear-gradient(160deg,#8a6a52,#d9a98c)"></div>
    <div class="stars"><svg class="on"><use href="#star"/></svg><svg class="on"><use href="#star"/></svg><svg class="on"><use href="#star"/></svg><svg class="off"><use href="#star"/></svg><svg class="off"><use href="#star"/></svg></div>
    <blockquote>“Lorem ipsum dolor sit amet, consectetur adipiscing elit. Donec et quam nunc. Nam tortor sapien, volutpat consectetur lacus ut, accumsan viverra urna. ”</blockquote>
    <cite>- Student Name</cite>
  </article>
</aside>

<footer class="site-footer" role="img" aria-label="Footer with a blue-tinted photo of a student studying at a laptop">
  <h3 style="left:60px;width:127px">Quick Links</h3>
  <h3 style="left:226px;width:213px">Contact Information</h3>
  <h3 style="left:479px;width:181px">Newsleter Signup</h3>
  <h3 style="left:698px;width:140px">Follow Us</h3>
  <ul class="abs qlinks"><li>Home</li><li>About</li><li>Search</li><li>Student</li><li>Tutor</li><li>Contacts</li></ul>
  <div class="abs cinfo">
    <div class="row"><svg viewBox="0 0 10 12"><path d="M5 0a4 4 0 0 0-4 4c0 3 4 8 4 8s4-5 4-8a4 4 0 0 0-4-4zm0 5.5A1.5 1.5 0 1 1 5 2.5a1.5 1.5 0 0 1 0 3z"/></svg>ABN 00112233445 Head Office, 48 Maple Grove Lane, Riverside Park, Kenton 4821<br>PO Box 310 Kenton DC 4821</div>
    <div class="row call"><svg viewBox="0 0 10 12" style="top:2px"><path d="M3 0l2 3-1.5 1.2c.4 1.6 1.3 3 2.6 3.9L7.5 7 10 9.5 8.3 12C4 11 .5 6 1 1z"/></svg>FREECALL 1800 555 012</div>
    <div class="row"><svg viewBox="0 0 12 9" style="width:10px"><path d="M0 0h12v9H0zM1 1l5 4 5-4"/></svg>info@lendyourlessons.com</div>
  </div>
  <div class="abs nl-text">Please enter your email address below to receive our FREE newsletter</div>
  <div class="abs nl-input">Your Email ID</div>
  <div class="btn btn-sub">Subscribe</div>
  <div class="abs follow"><div><i></i>Socialhub</div><div><i></i>Workline</div><div><i></i>Chirper</div><div><i></i>Email</div></div>
</footer>
<div class="bottom-bar"><span>Copyright@lendyourlessons.com. All Rights Are Reserved.</span><span>Join Us &nbsp;-&nbsp; Login to lendyourlessons Online &nbsp;-&nbsp; Support</span></div>
</body>
</html>
```